Cocktail-Making Assistant App re-design

Ok boys and girls, here's the deal:
I have an android app which is almost complete, but needs a design overhaul.

The app is a standard cocktail-making assistant: gives you a list of cocktails and the ability to see which cocktail you can make out of those ingredients (drinks, fruit, etc) you have at home.

I've attached some general app flow, as well as detailed requirements/explanation presentation. Most of those things are just FYI, so that you know what it's about.

3 screens are the most important (main screen, cocktail view screen, ingredient view screen), meaning I will pick the design mostly based on ideas for those 3 things, with the fourth being a rather simple list (given on attached flow, third tier)
Some other screens are derived from that, with some minor changes on it, but you shouldn't care about that.

There are lots of other, non-explained things which I said nothing about only because they are (from design point of view) completely the same and would only make it seem more complicated.

I don't want to influence the colour scheme, but the app will be released under RedFig developer name (having a light colured red fig as a logo) so I suppose some brownish design, for example, will not really fit nicely. If you, however, have a killer which you are confident will prove me wrong, I'm looking forward to seeing it!

It should be a serious, elegant look (as opposed to cartoonish, but we are not aiming for a business look at all!), not cluttered with details, no clubbing themes, glitter and so on.

Test apk file available on request (Android 2.3+).

Edit: payment is now guaranteed
Also please note that currently, the favorite, "heart" button has a motion effect:
on click it flies out of the screen to the left (white heart) and comes back to the screen as a red heart. Take that into consideration, if it means anything to you.

Target Market(s)

Whoever you imagine would enjoy drinking cocktails

Industry/Entity Type

Business

Requirements
Must have
• Everything is said in the provided documentation - images say more than I could possibly write here.
Nice to have
• As said, most of the icons are a nice-to-have. Only those which are critically linked to the rest of the design must be provided. More details in the docs.
Should not have
• No cartoon look, No zillion colours

```html
<!DOCTYPE html>
<html lang="en">
<head>
<meta charset="utf-8">
<title>151 Florida Bushwacker</title>
<link rel="stylesheet" href="https://fonts.googleapis.com/css2?family=Orbitron:wght@500;700&family=Arimo:ital,wght@1,400;1,700&display=swap">
<style>
  :root{
    --ink:#1f1f1f;
    --header-bg:#f1f1f1;
    --panel-bg:#f7f7f7;
    --rule:#d9d9d9;
    --accent-red:#d8161d;
    --green:#acd373;
    --orange:#fcb45e;
    --red:#fd6066;
    --tan:#d0aea3;
    --star-green:#9ccf6b;
    --star-orange:#f9b257;
    --star-red:#f0505a;
    --star-purple:#a99de6;
    --star-tan:#d7b8aa;
    --hint:#8a8a8a;
    --body-bg:#f4f4f4;
  }
  *{box-sizing:border-box;margin:0;padding:0}
  html,body{width:676px;height:1200px;overflow:hidden;background:var(--body-bg)}
  .screen{position:relative;width:676px;height:1200px;overflow:hidden;font-family:"Orbitron",sans-serif;color:var(--ink)}
  .app-header{position:absolute;left:0;top:0;width:676px;height:98px;background:linear-gradient(#fafafa,#ececec);}
  .app-header .divider{position:absolute;top:12px;width:1px;height:76px;background:var(--rule)}
  .back-home{position:absolute;left:8px;top:20px;display:flex;align-items:center}
  .title{position:absolute;left:150px;top:24px;font-size:24px;font-weight:700;letter-spacing:1.5px;line-height:31px;text-transform:uppercase}
  .camera{position:absolute;left:566px;top:28px}
  .accent-strip{position:absolute;left:0;top:96px;width:676px;height:10px;background:linear-gradient(var(--accent-red),#a50f14)}
  .summary{position:absolute;left:0;top:106px;width:676px;height:168px;background:var(--panel-bg)}
  .drink-photo{position:absolute;left:60px;top:22px;width:150px;height:114px;border-radius:8px;background:linear-gradient(135deg,#f6a63a,#e86f1f 45%,#6b2a16 80%,#93b54a)}
  .rating{position:absolute;left:256px;top:32px;display:flex;gap:10px}
  .rating-rule{position:absolute;left:256px;top:78px;width:248px;height:1px;background:var(--rule)}
  .vol{position:absolute;left:256px;top:90px;font-size:17px;font-weight:500;letter-spacing:1.5px;text-transform:uppercase}
  .fav{position:absolute;left:558px;top:42px}
  .ingredient{position:absolute;left:0;width:676px;height:138px}
  .ingredient .mark{position:absolute;left:113px;top:52px}
  .ingredient .name{position:absolute;left:190px;right:110px;text-align:center;font-size:18px;font-weight:500;letter-spacing:1.6px;text-transform:uppercase;line-height:31px}
  .ingredient .brand{display:block;font-size:12px;line-height:14px;color:#fff;letter-spacing:1.5px;text-align:left;padding-left:62px}
  .ingredient .cart{position:absolute;left:556px;top:22px}
  .green{top:274px;background:var(--green)}
  .orange{top:412px;background:var(--orange)}
  .red{top:549px;background:var(--red)}
  .tan{top:686px;height:136px;background:var(--tan)}
  .release{position:absolute;left:0;top:822px;width:676px;height:97px;background:linear-gradient(#fafafa,#e6e6e6)}
  .release p{position:absolute;left:52px;top:22px;font-size:13px;font-weight:500;letter-spacing:1.5px;color:var(--hint);text-transform:uppercase}
  .release .arrow{position:absolute;left:306px;top:50px}
  .release .notch{position:absolute;left:302px;top:82px;width:28px;height:28px;background:#fff;transform:rotate(45deg);border-left:1px solid var(--rule);border-top:1px solid var(--rule)}
  .details{position:absolute;left:0;top:919px;width:676px;height:281px;background:#fff;border-top:1px solid var(--rule);padding:22px 18px 0 19px;font-family:"Arimo",sans-serif;font-style:italic;font-size:11.4px;line-height:15px;color:#111}
  .details p+p{margin-top:15px}
  .mug{position:absolute;left:598px;top:1130px}
</style>
</head>
<body>
<main class="screen">
  <header class="app-header">
    <div class="back-home">
      <svg width="22" height="34" viewBox="0 0 22 34"><path d="M17 4 5 17l12 13" fill="none" stroke="var(--accent-red)" stroke-width="3"/></svg>
      <svg width="56" height="54" viewBox="0 0 56 54"><path d="M28 3 2 27h7v24h14V36h10v15h14V27h7L44 14V5h-7v3z" fill="var(--ink)"/></svg>
    </div>
    <span class="divider" style="left:130px"></span>
    <h1 class="title">151 Florida<br>Bushwacker</h1>
    <span class="divider" style="left:545px"></span>
    <svg class="camera" width="64" height="50" viewBox="0 0 64 50"><path d="M5 10h14l5-8h16l5 8h14a4 4 0 0 1 4 4v30a4 4 0 0 1-4 4H5a4 4 0 0 1-4-4V14a4 4 0 0 1 4-4z" fill="var(--ink)"/><circle cx="32" cy="28" r="13" fill="#f3f3f3"/><circle cx="32" cy="28" r="9" fill="var(--ink)"/><rect x="6" y="4" width="8" height="4" fill="var(--ink)"/></svg>
  </header>
  <div class="accent-strip"></div>

  <section class="summary">
    <div class="drink-photo" role="img" aria-label="Photo of assorted cocktails in glasses with fruit garnish"></div>
    <div class="rating" aria-label="Rating">
      <svg width="34" height="32" viewBox="0 0 24 23"><path d="M12 0l3 8h9l-7 5 3 9-8-6-8 6 3-9-7-5h9z" fill="var(--star-green)"/></svg>
      <svg width="34" height="32" viewBox="0 0 24 23"><path d="M12 0l3 8h9l-7 5 3 9-8-6-8 6 3-9-7-5h9z" fill="var(--star-orange)"/></svg>
      <svg width="34" height="32" viewBox="0 0 24 23"><path d="M12 0l3 8h9l-7 5 3 9-8-6-8 6 3-9-7-5h9z" fill="var(--star-red)"/></svg>
      <svg width="34" height="32" viewBox="0 0 24 23"><path d="M12 0l3 8h9l-7 5 3 9-8-6-8 6 3-9-7-5h9z" fill="var(--star-purple)"/></svg>
      <svg width="34" height="32" viewBox="0 0 24 23"><path d="M12 0l3 8h9l-7 5 3 9-8-6-8 6 3-9-7-5h9z" fill="var(--star-tan)"/></svg>
    </div>
    <div class="rating-rule"></div>
    <p class="vol">Vol unavailable</p>
    <svg class="fav" width="80" height="74" viewBox="0 0 80 74"><path d="M30 62 6 38C-4 28 2 6 18 6c6 0 10 3 12 7 2-4 6-7 12-7 16 0 22 22 12 32z" fill="#3a3a3a"/><circle cx="58" cy="50" r="21" fill="#3a3a3a" stroke="var(--panel-bg)" stroke-width="4"/><path d="M58 38v24M46 50h24" stroke="#fff" stroke-width="5"/></svg>
  </section>

  <section class="ingredient green">
    <svg class="mark" width="32" height="30" viewBox="0 0 24 23"><path d="M12 0l3 8h9l-7 5 3 9-8-6-8 6 3-9-7-5h9z" fill="#2b2b2b"/></svg>
    <p class="name" style="top:53px">1/2 oz Marisol rum</p>
    <svg class="cart" width="86" height="92" viewBox="0 0 86 92"><path d="M2 14h14l10 48h42" fill="none" stroke="#2b2b2b" stroke-width="7"/><path d="M18 24h62l-8 30H24z" fill="#2b2b2b"/><rect x="48" y="4" width="14" height="34" rx="4" transform="rotate(30 55 21)" fill="#2b2b2b" stroke="var(--green)" stroke-width="3"/><circle cx="30" cy="78" r="7" fill="#2b2b2b"/><circle cx="66" cy="78" r="7" fill="#2b2b2b"/><circle cx="18" cy="40" r="11" fill="#2b2b2b" stroke="var(--green)" stroke-width="3"/><path d="M12 40l4 4 8-8" fill="none" stroke="var(--green)" stroke-width="3"/></svg>
  </section>

  <section class="ingredient orange">
    <svg class="mark" width="32" height="30" viewBox="0 0 24 23"><path d="M12 0l3 8h9l-7 5 3 9-8-6-8 6 3-9-7-5h9z" fill="#2b2b2b"/></svg>
    <p class="name" style="top:53px">1/2 oz light rum</p>
    <svg class="cart" width="86" height="92" viewBox="0 0 86 92"><path d="M2 14h14l10 48h42" fill="none" stroke="#2b2b2b" stroke-width="7"/><path d="M18 24h62l-8 30H24z" fill="#2b2b2b"/><rect x="48" y="4" width="14" height="34" rx="4" transform="rotate(30 55 21)" fill="#2b2b2b" stroke="var(--orange)" stroke-width="3"/><circle cx="30" cy="78" r="7" fill="#2b2b2b"/><circle cx="66" cy="78" r="7" fill="#2b2b2b"/><circle cx="18" cy="40" r="11" fill="#2b2b2b" stroke="var(--orange)" stroke-width="3"/><path d="M18 34v12M12 40h12" stroke="var(--orange)" stroke-width="3"/></svg>
  </section>

  <section class="ingredient red">
    <svg class="mark" width="32" height="30" viewBox="0 0 24 23"><path d="M12 0l3 8h9l-7 5 3 9-8-6-8 6 3-9-7-5h9z" fill="#2b2b2b"/></svg>
    <p class="name" style="top:44px">1 oz 151 proof rum<span class="brand">Carvelo</span></p>
    <svg class="cart" width="86" height="92" viewBox="0 0 86 92"><path d="M2 14h14l10 48h42" fill="none" stroke="#2b2b2b" stroke-width="7"/><path d="M18 24h62l-8 30H24z" fill="#2b2b2b"/><rect x="48" y="4" width="14" height="34" rx="4" transform="rotate(30 55 21)" fill="#2b2b2b" stroke="var(--red)" stroke-width="3"/><circle cx="30" cy="78" r="7" fill="#2b2b2b"/><circle cx="66" cy="78" r="7" fill="#2b2b2b"/><circle cx="18" cy="40" r="11" fill="#2b2b2b" stroke="var(--red)" stroke-width="3"/><path d="M18 34v12M12 40h12" stroke="var(--red)" stroke-width="3"/></svg>
  </section>

  <section class="ingredient tan">
    <svg class="mark" width="32" height="30" viewBox="0 0 24 23" style="top:48px"><path d="M12 0l3 8h9l-7 5 3 9-8-6-8 6 3-9-7-5h9z" fill="#2b2b2b"/></svg>
    <p class="name" style="top:66px">1 oz dark creme<br>de cacao</p>
    <svg class="cart" width="86" height="92" viewBox="0 0 86 92"><path d="M2 14h14l10 48h42" fill="none" stroke="#2b2b2b" stroke-width="7"/><path d="M18 24h62l-8 30H24z" fill="#2b2b2b"/><rect x="48" y="4" width="14" height="34" rx="4" transform="rotate(30 55 21)" fill="#2b2b2b" stroke="var(--tan)" stroke-width="3"/><circle cx="30" cy="78" r="7" fill="#2b2b2b"/><circle cx="66" cy="78" r="7" fill="#2b2b2b"/><circle cx="18" cy="40" r="11" fill="#2b2b2b" stroke="var(--tan)" stroke-width="3"/><path d="M12 40l4 4 8-8" fill="none" stroke="var(--tan)" stroke-width="3"/></svg>
  </section>

  <section class="release">
    <p>Release to hide details about making this cocktail.</p>
    <svg class="arrow" width="20" height="22" viewBox="0 0 20 22"><path d="M10 1v18M3 12l7 7 7-7" fill="none" stroke="#6a6a6a" stroke-width="3"/></svg>
    <div class="notch"></div>
  </section>

  <article class="details">
    <p>Contrary to popular belief, Lorem Ipsum is not simply random text. It has roots in a piece of classical Latin literature from 45 BC, making it over 2000 years old. Daniel Ferrow, a Latin professor at Ashgrove College in Vermont, looked up one of the more obscure Latin words, consectetur, from a Lorem Ipsum passage, and going through the cites of the word in classical literature, discovered the undoubtable source. Lorem Ipsum comes from sections 1.10.32 and 1.10.33 of "de Finibus Bonorum et Malorum" (The Extremes of Good and Evil) by Marcus Vell, written in 45 BC. This book is a treatise on the theory of ethics, very popular during the Renaissance. The first line of Lorem Ipsum, "Lorem ipsum dolor sit amet..", comes from a line in section 1.10.32.</p>
    <p>The standard chunk of Lorem Ipsum used since the 1500s is reproduced below for those interested. Sections 1.10.32 and 1.10.33 from "de Finibus Bonorum et Malorum" by Marcus Vell are also reproduced in their exact original form, accompanied by English versions from the 1914 translation by H. Dorran.</p>
  </article>
  <svg class="mug" width="62" height="62" viewBox="0 0 62 62"><path d="M6 14a8 8 0 0 1 10-8 9 9 0 0 1 16-2 8 8 0 0 1 12 6v4z" fill="#2b2b2b"/><rect x="6" y="14" width="38" height="46" rx="3" fill="#2b2b2b"/><path d="M44 24h8a6 6 0 0 1 6 6v12a6 6 0 0 1-6 6h-8" fill="none" stroke="#2b2b2b" stroke-width="6"/><path d="M16 24v28M25 24v28M34 24v28" stroke="#f4f4f4" stroke-width="3"/></svg>
</main>
</body>
</html>
```